NEW Modern Sleek Business Card for VR Language Startup

Our startup is using VR to lead the next wave of world language education. We need a two-sided business card that introduces the larger organization (Veyloria Language Inc) and our contact info on one side and shows the product, Glimwoorld, on the other side.

Side 1 (contact info)= Veyloria Logo and Contact info (name, title, phone, email)

Side 2 (product)= Glimworld logo, text, and website
Text= Culturally Immersive Language Learning Games
Website= www.glimworld-play.com

Target Market(s)

Education, Technology

Contact Information for Business Card

Contact info will be updated upon approval of the design. For now, put this as a placeholder.

Perry Dunmore
Founder & CEO
pdunmore@quillpost-mail.net
(555)-014-2286

Font styles to use
Other font styles liked:
• Gibson and Century Gothic are the brand fonts

Requirements
Nice to have
• I would love to see cohesion between the design and colors of the two logos. I have attached a few business card designs that I like, so you can get a feel for my preferred style.

```html
<!DOCTYPE html>
<html lang="en">
<head>
<meta charset="utf-8">
<title>Veyloria Language – Business Card</title>
<link href="https://fonts.googleapis.com/css2?family=Lato:wght@300;400;700&display=swap" rel="stylesheet">
<style>
  :root {
    --backdrop: #3b3532;
    --card: #0c0c0c;
    --ink: #f4f4f4;
    --muted: #c9c9c9;
    --divider: #3a3a3a;
    --link: #3d8bff;
    --warm-a: #ff4d6d;
    --warm-b: #a45cff;
    --warm-c: #3aa0ff;
    --cool-a: #1fd3f0;
    --cool-b: #5a6cff;
  }
  * { margin: 0; padding: 0; box-sizing: border-box; }
  html, body {
    width: 1200px; height: 844px; overflow: hidden;
    background: var(--backdrop);
    font-family: "Lato", "Century Gothic", sans-serif;
  }
  .sheet {
    width: 1200px; height: 844px;
    display: flex; align-items: center; justify-content: center; gap: 48px;
  }
  .card {
    width: 540px; height: 308px;
    background: var(--card);
    border-radius: 4px;
    box-shadow: 0 18px 40px rgba(0,0,0,.55);
    position: relative;
    color: var(--ink);
  }

  /* Contact side */
  .card--contact { display: flex; align-items: center; }
  .brand-block {
    width: 50%; height: 100%;
    display: flex; flex-direction: column; align-items: center; justify-content: center; gap: 18px;
  }
  .brand-mark {
    width: 74px; height: 74px; border-radius: 50%;
    background: linear-gradient(135deg, var(--warm-a), var(--warm-b) 55%, var(--warm-c));
  }
  .brand-name {
    font-weight: 700; font-size: 32px; letter-spacing: 4px;
    text-transform: uppercase; color: var(--ink);
  }
  .card-divider {
    width: 1px; height: 150px; background: var(--divider);
  }
  .contact-block { padding-left: 26px; }
  .person-name {
    font-size: 22px; font-weight: 400; letter-spacing: .5px; text-transform: uppercase;
    background: linear-gradient(90deg, var(--warm-a), var(--warm-b) 50%, var(--warm-c));
    -webkit-background-clip: text; background-clip: text; color: transparent;
  }
  .person-title { font-size: 15px; color: var(--ink); margin-bottom: 14px; }
  .contact-line {
    display: flex; align-items: center; gap: 7px;
    font-size: 14px; color: var(--ink); margin-bottom: 5px;
  }
  .contact-line svg { flex: none; }

  /* Product side */
  .card--product {
    display: flex; flex-direction: column; align-items: center; justify-content: center;
  }
  .product-mark {
    width: 84px; height: 84px; border-radius: 50%;
    background: linear-gradient(135deg, var(--cool-a), var(--cool-b));
    margin-bottom: 16px;
  }
  .product-name {
    font-size: 40px; font-weight: 400; color: var(--cool-a); margin-bottom: 14px;
  }
  .product-tagline {
    font-size: 13.5px; letter-spacing: .6px; text-transform: uppercase;
    color: var(--muted); margin-bottom: 14px;
  }
  .product-url { font-size: 14px; letter-spacing: 1px; color: var(--link); }
</style>
</head>
<body>
<main class="sheet">
  <section class="card card--contact">
    <div class="brand-block">
      <div class="brand-mark"></div>
      <div class="brand-name">Veyloria</div>
    </div>
    <div class="card-divider"></div>
    <div class="contact-block">
      <h1 class="person-name">Perry Dunmore</h1>
      <p class="person-title">Founder &amp; CEO</p>
      <p class="contact-line">
        <svg width="14" height="14" viewBox="0 0 14 14" aria-hidden="true">
          <path d="M3 1.5l2.2 2.3-1.3 1.6a8 8 0 0 0 4.7 4.7l1.6-1.3 2.3 2.2-1.4 1.6C6.6 12.6 1.4 7.4 1.4 2.9z" fill="#ff6a5a"/>
        </svg>
        (555)-014-2286
      </p>
      <p class="contact-line">
        <svg width="14" height="11" viewBox="0 0 14 11" aria-hidden="true">
          <rect x="0.5" y="0.5" width="13" height="10" rx="1" fill="#6a7cff"/>
          <path d="M1 1.2l6 4.6 6-4.6" stroke="#0c0c0c" stroke-width="1.2" fill="none"/>
        </svg>
        pdunmore@quillpost-mail.net
      </p>
    </div>
  </section>

  <section class="card card--product">
    <div class="product-mark"></div>
    <div class="product-name">Glimworld</div>
    <p class="product-tagline">Culturally Immersive Language Learning Games</p>
    <p class="product-url">www.glimworld-play.com</p>
  </section>
</main>
</body>
</html>
```